Puddle Moss sleep comforter 'Local campaign' Billboard design

Billboard will be on display in a busy local street of Coburg. We want this to appeal to the fact that we are locals, we are mums, we care about mums, our factory is here, our staff are here and we support the community here. We like a possible support angle through the isolation of covid. For the purpose of design please refer to our:
Facebook: https://www.facebook.com/puddlemossnaptoys
Insta: https://www.instagram.com/puddlemoss_naptoys
Or www.puddlemossandkin.com

Designs look the same

```html
<!DOCTYPE html>
<html lang="en">
<head>
<meta charset="utf-8">
<title>Puddle Moss – Sleep Makes Babies Happy!</title>
<link rel="stylesheet" href="https://fonts.googleapis.com/css2?family=Lobster&family=Montserrat:ital,wght@0,800;1,800&display=swap">
<style>
  :root {
    --mist: #e0e5eb;
    --stone: #c4c5c5;
    --tan: #d4a574;
    --ink: #0c0c0c;
    --white: #ffffff;
    --rust: #b9712f;
  }
  html, body {
    margin: 0;
    padding: 0;
    width: 1200px;
    height: 672px;
    overflow: hidden;
    background: var(--mist);
  }
  .billboard {
    position: relative;
    width: 1200px;
    height: 672px;
    overflow: hidden;
    background: var(--mist);
  }
  .backdrop {
    position: absolute;
    inset: 0;
  }
  .hero-photo {
    position: absolute;
    left: 0;
    top: 0;
    width: 660px;
    height: 672px;
    background:
      linear-gradient(200deg, rgba(224,229,235,0) 55%, rgba(185,113,47,0.9) 85%),
      radial-gradient(ellipse 40% 35% at 45% 50%, #f3d7cc 0%, #f6ebe7 60%, rgba(246,246,248,0) 100%),
      linear-gradient(90deg, #f4f4f6 0%, #f1f2f5 70%, rgba(224,229,235,0) 100%);
  }
  .brand-badge {
    position: absolute;
    left: 839px;
    top: 38px;
    width: 316px;
    height: 316px;
    border-radius: 50%;
    background: var(--ink);
    display: flex;
    align-items: center;
    justify-content: center;
    text-align: center;
  }
  .brand-name {
    font-family: "Montserrat", sans-serif;
    font-weight: 800;
    font-size: 40px;
    line-height: 1.05;
    color: var(--white);
  }
  .headline {
    position: absolute;
    inset: 0;
  }
  .headline text {
    font-family: "Lobster", cursive;
    font-size: 106px;
    stroke-linejoin: round;
    paint-order: stroke fill;
  }
  .headline .shadow { fill: var(--ink); stroke: var(--ink); stroke-width: 12px; }
  .headline .line-top { fill: var(--tan); stroke: var(--white); stroke-width: 9px; }
  .headline .line-bottom { fill: var(--ink); stroke: var(--white); stroke-width: 9px; }
  .web-address {
    position: absolute;
    right: 44px;
    top: 612px;
    display: flex;
    align-items: center;
    gap: 10px;
    font-family: "Montserrat", sans-serif;
    font-style: italic;
    font-weight: 800;
    font-size: 25px;
    line-height: 1;
    color: var(--ink);
    white-space: nowrap;
  }
  .web-address svg { width: 21px; height: 21px; flex: none; }
  .frame {
    position: absolute;
    left: 19px;
    top: 18px;
    right: 19px;
    bottom: 18px;
    border: 3px solid var(--white);
    pointer-events: none;
  }
</style>
</head>
<body>
<main class="billboard">
  <svg class="backdrop" viewBox="0 0 1200 672" width="1200" height="672" aria-hidden="true">
    <rect width="1200" height="672" fill="var(--mist)"/>
    <polygon points="727,0 1200,0 1200,672 675,672 876,177" fill="var(--stone)"/>
    <polygon points="433,672 857,214 675,672" fill="var(--tan)"/>
  </svg>

  <div class="hero-photo" role="img" aria-label="Photo of a newborn baby sleeping on soft white fur, tucked under a rust-coloured blanket"></div>

  <svg class="backdrop" viewBox="0 0 1200 672" width="1200" height="672" aria-hidden="true">
    <polygon points="347,0 594,0 843,144 834,154" fill="var(--ink)"/>
  </svg>

  <div class="brand-badge">
    <span class="brand-name">Puddle<br>Moss</span>
  </div>

  <svg class="headline" viewBox="0 0 1200 672" width="1200" height="672" aria-label="Sleep Makes Babies Happy!">
    <g transform="rotate(-16 855 515)">
      <text class="shadow" x="863" y="471" text-anchor="middle">Sleep Makes</text>
      <text class="line-top" x="855" y="465" text-anchor="middle">Sleep Makes</text>
      <text class="shadow" x="858" y="576" text-anchor="middle">Babies Happy!</text>
      <text class="line-bottom" x="850" y="570" text-anchor="middle">Babies Happy!</text>
    </g>
  </svg>

  <div class="web-address">
    <svg viewBox="0 0 24 24" aria-hidden="true">
      <g fill="none" stroke="var(--ink)" stroke-width="2">
        <circle cx="12" cy="12" r="10"/>
        <ellipse cx="12" cy="12" rx="4.5" ry="10"/>
        <line x1="2" y1="12" x2="22" y2="12"/>
        <path d="M4 7h16M4 17h16"/>
      </g>
    </svg>
    <span>www.puddlemossandkin.com</span>
  </div>

  <div class="frame"></div>
</main>
</body>
</html>
```